Coastal Learner Bureau business cards

Australian company about to start offering its services. We recruit international students to come to study English, vocational education and postgraduate courses in Australia. We help them find the institution and select the right city they want to come to Australia. We are a young, online oriented and supportive agency. Our clients are between 18 and 35 years old, mainly University students, young professionals or people with work experience. We provide much more information that any other agency offer. We administrate a Facebook group with more than 11.000 members that daily ask questions about general information when coming to Australia, while they are here and even after they leave the country

Target Market(s)

International students from South America, Central America and Europe

Industry/Entity Type

Student

Contact Information for Business Card

Tomas Bilbrea
Managing Director
tomas@kelvarin.com.au
www.kelvoria.com.au
+61 491058264
Melbourne, Australia

Font styles to use
Serif
Sans Serif

Colors

Designer to choose colors to be used in the design.

Requirements
Must have
• Horizontal design
• Standard business card size and shape. If font uses green or yellow colours, they will have to match the ones from the logo
Nice to have
• UPDATE: Use the contents of the green image to design one of the card sides. Use our logo in the background of that side as watermark.
• Passport image, or immigration stamps. A picture of the Yarra River (from Melbourne) would be cool as well.
Should not have
• Non-standard business card size and shape
• Not black as the background colour of any sides as we are not a VIP agency or a hight class service. We are orientes to young people and they like colours, pictures, something attractive.
• Vertical design
• NO YELLOW or BLACK AS THE BACKGROUND COLOUR OF ANY SIDE OF THE BIZ CARD

```html
<!DOCTYPE html>
<html lang="es">
<head>
<meta charset="utf-8">
<title>Coastal Learner Bureau — Business Cards</title>
<link rel="stylesheet" href="https://fonts.googleapis.com/css2?family=Open+Sans:wght@400;600;700&family=Noto+Serif:wght@700&display=swap">
<style>
  :root {
    --stage: #eeeeef;
    --card-white: #ffffff;
    --brand-yellow: #e8bb14;
    --brand-green: #0f6a3a;
    --ink: #3a3a3a;
    --shadow: rgba(0, 0, 0, 0.12);
  }
  * { margin: 0; padding: 0; box-sizing: border-box; }
  html, body {
    width: 1200px;
    height: 900px;
    overflow: hidden;
    background: var(--stage);
    font-family: "Open Sans", Arial, sans-serif;
  }
  .stage {
    position: relative;
    width: 1200px;
    height: 900px;
  }
  .card {
    position: absolute;
    top: 307px;
    width: 500px;
    height: 286px;
    border-radius: 2px;
    box-shadow: 0 6px 18px var(--shadow);
    overflow: hidden;
  }
  .card--front { left: 60px; background: var(--card-white); }
  .card--back  { left: 640px; background: var(--brand-green); }

  /* Front side */
  .holder {
    position: absolute;
    top: 30px;
    left: 32px;
  }
  .holder__name {
    font-size: 17px;
    font-weight: 700;
    letter-spacing: 0.5px;
    text-transform: uppercase;
  }
  .holder__first { color: var(--brand-yellow); }
  .holder__last  { color: var(--brand-green); }
  .holder__role {
    font-size: 11px;
    color: var(--ink);
    margin-top: 1px;
  }
  .contacts {
    position: absolute;
    left: 32px;
    top: 112px;
    list-style: none;
  }
  .contacts__item {
    display: flex;
    align-items: center;
    gap: 7px;
    font-size: 11px;
    color: var(--ink);
    line-height: 17px;
  }
  .contacts__icon { width: 9px; height: 9px; flex: none; }

  .wordmark {
    display: flex;
    align-items: center;
    gap: 8px;
    font-family: "Open Sans", Arial, sans-serif;
    font-weight: 700;
    line-height: 1;
    color: var(--brand-green);
  }
  .wordmark__dot {
    border-radius: 50%;
    background: var(--brand-yellow);
    flex: none;
  }
  .card--front .wordmark {
    position: absolute;
    left: 300px;
    top: 122px;
    font-size: 32px;
  }
  .card--front .wordmark__dot { width: 14px; height: 14px; }

  .location {
    position: absolute;
    right: 34px;
    bottom: 30px;
    font-size: 12px;
    color: var(--ink);
  }

  /* Back side */
  .card--back .brand-block {
    position: absolute;
    inset: 0;
    display: flex;
    flex-direction: column;
    align-items: center;
    justify-content: center;
    gap: 16px;
  }
  .card--back .wordmark { font-size: 40px; color: var(--card-white); }
  .card--back .wordmark__dot { width: 16px; height: 16px; background: var(--brand-yellow); }
  .tagline {
    font-family: "Noto Serif", Georgia, serif;
    font-weight: 700;
    font-size: 13px;
    letter-spacing: 1px;
    color: var(--card-white);
  }
</style>
</head>
<body>
<main class="stage">

  <section class="card card--front" aria-label="Card front">
    <div class="holder">
      <p class="holder__name"><span class="holder__first">Tomas</span> <span class="holder__last">Bilbrea</span></p>
      <p class="holder__role">Managing Director</p>
    </div>

    <ul class="contacts">
      <li class="contacts__item">
        <svg class="contacts__icon" viewBox="0 0 10 10" aria-hidden="true">
          <path d="M2 0.8 L3.6 0.8 L4.2 3 L3 3.8 Q4 6 6.2 7 L7 5.8 L9.2 6.4 L9.2 8 Q9.2 9.2 8 9.2 Q1 8.6 0.8 2 Q0.8 0.8 2 0.8Z" fill="var(--brand-yellow)"/>
        </svg>
        +61 491058264
      </li>
      <li class="contacts__item">
        <svg class="contacts__icon" viewBox="0 0 10 10" aria-hidden="true">
          <rect x="0.5" y="2" width="9" height="6.5" rx="1" fill="var(--brand-yellow)"/>
          <path d="M0.8 2.4 L5 5.6 L9.2 2.4" stroke="#fff" stroke-width="0.9" fill="none"/>
        </svg>
        tomas@kelvarin.com.au
      </li>
      <li class="contacts__item">
        <svg class="contacts__icon" viewBox="0 0 10 10" aria-hidden="true">
          <circle cx="5" cy="5" r="4.5" fill="var(--brand-yellow)"/>
          <path d="M0.5 5 H9.5 M5 0.5 Q2.5 5 5 9.5 M5 0.5 Q7.5 5 5 9.5" stroke="#fff" stroke-width="0.7" fill="none"/>
        </svg>
        www.kelvoria.com.au
      </li>
    </ul>

    <div class="wordmark"><span class="wordmark__dot"></span>Kelvoria</div>

    <p class="location">Melbourne, Australia</p>
  </section>

  <section class="card card--back" aria-label="Card back">
    <div class="brand-block">
      <div class="wordmark"><span class="wordmark__dot"></span>Kelvoria</div>
      <p class="tagline">HACEMOS MÁS POR TI!</p>
    </div>
  </section>

</main>
</body>
</html>
```